Business Card Design Project for Heron Lending

Hello there,

We are looking for a business card design for our new Heron Lending car financing company. We are looking for a business card that will include:

- An address
- Telephone number and extension
- Employee Name
- Employee Title
- Our logo and name clearly visible

We are including our logo with this writeup, we are looking to convey friendliness, trus and memorability. Colors and everything else is up to you.

Target Market(s)

18-34 year old males and females

Industry/Entity Type

Business

```html
<!DOCTYPE html>
<html lang="en">
<head>
<meta charset="utf-8">
<title>Heron Lending – Business Card</title>
<link rel="stylesheet" href="https://fonts.googleapis.com/css2?family=Open+Sans:wght@400;700&display=swap">
<style>
  :root {
    --backdrop: #e9e9ea;
    --card-front: #ffffff;
    --card-back: #f1f1ef;
    --ink-teal: #123f55;
    --ink-dark: #2a2a2a;
    --art-tone: #8c8c8c;
    --art-tone-light: #d6d6d4;
    --card-shadow: rgba(0, 0, 0, 0.12);
  }
  * { margin: 0; padding: 0; box-sizing: border-box; }
  html, body {
    width: 1200px;
    height: 675px;
    overflow: hidden;
    background: var(--backdrop);
    font-family: "Open Sans", Arial, sans-serif;
  }
  .stage {
    width: 1200px;
    height: 675px;
    display: flex;
    align-items: center;
    justify-content: center;
    gap: 40px;
  }
  .card {
    position: relative;
    width: 520px;
    height: 297px;
    box-shadow: 0 6px 18px var(--card-shadow);
  }
  .card--front { background: var(--card-front); }
  .card--back { background: var(--card-back); }

  .brand {
    position: absolute;
    display: flex;
    flex-direction: column;
    align-items: center;
  }
  .brand__art {
    background: linear-gradient(135deg, var(--art-tone-light), var(--art-tone));
    border-radius: 4px;
  }
  .brand__name {
    color: var(--ink-teal);
    font-weight: 400;
    letter-spacing: 0.06em;
    white-space: nowrap;
  }
  .card--front .brand {
    left: 50%;
    top: 58px;
    transform: translateX(-50%);
  }
  .card--front .brand__art { width: 210px; height: 120px; }
  .card--front .brand__name { font-size: 26px; margin-top: 10px; }

  .card--back .brand {
    right: 36px;
    top: 34px;
  }
  .card--back .brand__art { width: 160px; height: 86px; }
  .card--back .brand__name { font-size: 19px; margin-top: 6px; }

  .person {
    position: absolute;
    left: 38px;
    top: 128px;
    color: var(--ink-teal);
  }
  .person__name { font-size: 15px; font-weight: 700; line-height: 1.3; }
  .person__title { font-size: 11px; font-weight: 400; }

  .contact {
    position: absolute;
    left: 38px;
    bottom: 30px;
    list-style: none;
    color: var(--ink-teal);
    font-size: 12px;
  }
  .contact__item {
    display: flex;
    align-items: center;
    gap: 7px;
    line-height: 1.6;
  }
  .contact__icon { width: 11px; height: 11px; fill: var(--ink-teal); flex: none; }
</style>
</head>
<body>
  <main class="stage">
    <section class="card card--front" aria-label="Business card front">
      <div class="brand">
        <div class="brand__art" role="img" aria-label="Brand illustration area: walking animal in black and white"></div>
        <div class="brand__name">Heron Lending</div>
      </div>
    </section>

    <section class="card card--back" aria-label="Business card back">
      <div class="brand">
        <div class="brand__art" role="img" aria-label="Brand illustration area: walking animal in black and white"></div>
        <div class="brand__name">Heron Lending</div>
      </div>

      <div class="person">
        <p class="person__name">Your Long Name</p>
        <p class="person__title">Your Title</p>
      </div>

      <ul class="contact">
        <li class="contact__item">
          <svg class="contact__icon" viewBox="0 0 24 24" aria-hidden="true">
            <path d="M6.6 10.8a15.1 15.1 0 0 0 6.6 6.6l2.2-2.2c.3-.3.7-.4 1-.2 1.1.4 2.3.6 3.6.6.6 0 1 .4 1 1V20c0 .6-.4 1-1 1A17 17 0 0 1 3 4c0-.6.4-1 1-1h3.5c.6 0 1 .4 1 1 0 1.3.2 2.5.6 3.6.1.3 0 .7-.2 1z"/>
          </svg>
          <span>00.00.00.0000</span>
        </li>
        <li class="contact__item">
          <svg class="contact__icon" viewBox="0 0 24 24" aria-hidden="true">
            <path d="M12 2a7 7 0 0 0-7 7c0 5.2 7 13 7 13s7-7.8 7-13a7 7 0 0 0-7-7zm0 9.5A2.5 2.5 0 1 1 12 6.5a2.5 2.5 0 0 1 0 5z"/>
          </svg>
          <span>Your Commercial or office address</span>
        </li>
      </ul>
    </section>
  </main>
</body>
</html>
```